Veterinary Pylon

My veterinary clinic is not clearly visible from the street and I want to place a Pylon next to my driveway. I want a modern, elegant straight Design, the Photo shows the sheduled place. One can see the clinic on our Homepage: www.tailbright-vethaus.at
The last pictures are examples for pylones I like

Target Market(s)

the passing cars often miss my entry...I want to show where to turn left

Colors
3276b5
33a6d7
00a990

Requirements
Must have
• High value, simple elegance, size: 250cm (high) x 100cm (width)
Nice to have
• Our Logo, arrow(?)

A special Text is not necessary but this will be an option:

Biegen sie hier ab und wir biegen es wieder hin!
Should not have
• Too much Color, the colors I have chosen are the possible colors but it‘s not necessary to use them.

```html
<!DOCTYPE html>
<html lang="de">
<head>
<meta charset="UTF-8">
<title>Tailbright Vethaus – Pylon</title>
<link rel="stylesheet" href="https://fonts.googleapis.com/css2?family=Archivo+Black&display=swap">
<style>
  :root {
    --navy: #114a8f;
    --sky: #2cb9dc;
    --white: #ffffff;
    --mist: #e4ebf4;
  }
  html, body {
    margin: 0;
    padding: 0;
    overflow: hidden;
    background: var(--white);
  }
  .pylon {
    position: relative;
    width: 1200px;
    height: 3000px;
    background: var(--white);
    overflow: hidden;
    font-family: "Archivo Black", "Arial Black", sans-serif;
  }
  .band-top {
    position: absolute;
    left: 0; top: 0;
    width: 100%; height: 33px;
    background: var(--sky);
  }
  .band-bottom {
    position: absolute;
    left: 0; bottom: 0;
    width: 100%; height: 46px;
    background: var(--navy);
  }
  .brand-dot {
    position: absolute;
    left: 410px; top: 300px;
    width: 380px; height: 380px;
    border-radius: 50%;
    background: linear-gradient(90deg, var(--navy), var(--sky));
  }
  .brand-name {
    position: absolute;
    left: 0; top: 860px;
    width: 100%;
    margin: 0;
    text-align: center;
    color: var(--navy);
    font-weight: 400;
    font-size: 132px;
    line-height: 1.12;
    letter-spacing: 1px;
    text-transform: uppercase;
  }
  .turn-sign {
    position: absolute;
    left: 365px; top: 1474px;
    width: 484px; height: 484px;
  }
  .brand-echo {
    position: absolute;
    left: 0; top: 2230px;
    width: 100%;
    margin: 0;
    text-align: center;
    color: var(--mist);
    font-weight: 400;
    font-size: 160px;
    line-height: 1.15;
    text-transform: uppercase;
    -webkit-mask-image: linear-gradient(to bottom, #000 60%, transparent 100%);
            mask-image: linear-gradient(to bottom, #000 60%, transparent 100%);
  }
</style>
</head>
<body>
  <main class="pylon">
    <div class="band-top"></div>

    <div class="brand-dot" aria-hidden="true"></div>
    <h1 class="brand-name">Tailbright<br>Vethaus</h1>

    <svg class="turn-sign" viewBox="0 0 484 484" role="img" aria-label="Hier links abbiegen">
      <defs>
        <linearGradient id="turnFill" x1="0" y1="0" x2="1" y2="0">
          <stop offset="0" stop-color="#114a8f"/>
          <stop offset="1" stop-color="#2cb9dc"/>
        </linearGradient>
      </defs>
      <circle cx="242" cy="242" r="242" fill="url(#turnFill)"/>
      <g fill="none" stroke="#ffffff" stroke-width="26">
        <line x1="112" y1="240" x2="384" y2="240"/>
        <polyline points="212,134 106,240 212,346"/>
      </g>
    </svg>

    <p class="brand-echo" aria-hidden="true">Tailbright<br>Vethaus</p>

    <div class="band-bottom"></div>
  </main>
</body>
</html>
```